New Business Card Design

We would like to refresh our business cards and make them look better. We are an IT company specialising in Cloud Services, IT Managed Services, software and hardware. I have attached a PSD of our current design. Also attached our logo.
Updates

I have uploaded all new logos in EPS format.

Can you please edit all designs to include a job title for Marcus Hollis, eg. General Manager

Industry/Entity Type

Software

Colors
ffffff

Requirements
Must have
• Please use white background.
Should not have
• Black background

```html
<!DOCTYPE html>
<html lang="en">
<head>
<meta charset="utf-8">
<title>Meridian Systems – Business Card</title>
<link href="https://fonts.googleapis.com/css2?family=Questrial&family=Open+Sans:wght@400;700&display=swap" rel="stylesheet">
<style>
  :root {
    --stage: #ecebe8;
    --card: #ffffff;
    --ink: #2b3138;
    --ink-soft: #4a4f55;
    --accent: #c0392b;
    --band: #8a939c;
    --band-line: #b7bdc3;
    --faint: #f3e4e2;
    --divider: #d6d9dc;
  }
  * { box-sizing: border-box; margin: 0; padding: 0; }
  html, body { width: 1200px; height: 720px; overflow: hidden; }
  body {
    background: var(--stage);
    font-family: "Open Sans", Arial, sans-serif;
    position: relative;
  }
  .card {
    position: absolute;
    width: 520px;
    height: 300px;
    background: var(--card);
    box-shadow: 0 6px 18px rgba(0,0,0,0.12);
    overflow: hidden;
  }
  .card--front { left: 50px; top: 90px; }
  .card--back { left: 630px; top: 330px; }

  .swoosh { position: absolute; inset: 0; width: 100%; height: 100%; }

  .brand {
    position: absolute;
    display: flex;
    align-items: center;
    font-family: "Questrial", "Century Gothic", sans-serif;
    color: var(--ink);
    font-weight: 400;
    white-space: nowrap;
  }
  .brand__dot {
    border-radius: 50%;
    background: var(--accent);
    flex: none;
  }
  .card--front .brand { left: 30px; top: 100px; width: 250px; gap: 10px; }
  .card--front .brand__dot { width: 24px; height: 24px; }
  .card--front .brand__name { font-size: 19px; letter-spacing: 2.5px; }

  .divider {
    position: absolute;
    left: 292px; top: 24px;
    width: 1px; height: 84px;
    background: var(--divider);
  }
  .contact {
    position: absolute;
    left: 306px; top: 24px;
    list-style: none;
    font-size: 11.5px;
    color: var(--ink-soft);
  }
  .contact li {
    display: flex;
    align-items: center;
    gap: 8px;
    height: 21px;
  }
  .contact svg { width: 12px; height: 12px; flex: none; }

  .holder {
    position: absolute;
    left: 54px; top: 226px;
    color: #fff;
    line-height: 1.25;
  }
  .holder__name { font-weight: 700; font-size: 15px; }
  .holder__title { font-size: 12px; }

  .backdrop {
    position: absolute;
    left: 185px; top: 22px;
    width: 170px; height: 170px;
    border-radius: 50%;
    background: var(--faint);
  }
  .card--back .brand {
    left: 0; right: 0; top: 92px;
    justify-content: center;
  }
  .card--back .brand__name { font-size: 38px; letter-spacing: 6px; }
  .tagline {
    position: absolute;
    left: 0; right: 0; top: 216px;
    text-align: center;
    font-size: 14.5px;
    line-height: 1.45;
    color: var(--ink-soft);
  }
</style>
</head>
<body>

<section class="card card--front" aria-label="Business card front">
  <svg class="swoosh" viewBox="0 0 520 300" aria-hidden="true">
    <path d="M0,172 C150,187 330,137 520,119" fill="none" stroke="var(--band-line)" stroke-width="1.5"/>
    <path d="M0,178 C150,193 330,143 520,125" fill="none" stroke="var(--accent)" stroke-width="3"/>
    <path d="M0,186 C150,201 330,151 520,133 L520,168 C380,190 200,258 0,300 Z" fill="var(--band)"/>
    <path d="M40,300 C210,250 380,195 520,176" fill="none" stroke="var(--accent)" stroke-width="2.5"/>
  </svg>

  <div class="brand">
    <span class="brand__dot"></span>
    <span class="brand__name">meridian systems</span>
  </div>

  <div class="divider"></div>
  <ul class="contact">
    <li>
      <svg viewBox="0 0 12 12"><circle cx="6" cy="6" r="6" fill="var(--accent)"/><path d="M4,3 L5,3 L5.5,4.6 L4.8,5.2 Q5.5,6.6 6.8,7.2 L7.4,6.5 L9,7 L9,8 Q8,9 6.2,8 Q4,6.6 3.4,4.6 Q3.2,3.4 4,3Z" fill="#fff"/></svg>
      <span>07 3555 0148</span>
    </li>
    <li>
      <svg viewBox="0 0 12 12"><circle cx="6" cy="6" r="6" fill="var(--accent)"/><rect x="4.2" y="2.6" width="3.6" height="6.8" rx="0.6" fill="#fff"/></svg>
      <span>0400 555 217</span>
    </li>
    <li>
      <svg viewBox="0 0 12 12"><circle cx="6" cy="6" r="6" fill="var(--accent)"/><rect x="3" y="4" width="6" height="4.2" fill="#fff"/><path d="M3,4 L6,6.4 L9,4" fill="none" stroke="var(--accent)" stroke-width="0.8"/></svg>
      <span>mhollis@meridianit.com.au</span>
    </li>
    <li>
      <svg viewBox="0 0 12 12"><circle cx="6" cy="6" r="6" fill="var(--accent)"/><circle cx="6" cy="6" r="3" fill="none" stroke="#fff" stroke-width="0.9"/><path d="M3,6 H9 M6,3 V9" stroke="#fff" stroke-width="0.8"/></svg>
      <span>www.meridianit.com.au</span>
    </li>
  </ul>

  <div class="holder">
    <p class="holder__name">Marcus Hollis</p>
    <p class="holder__title">General Manager</p>
  </div>
</section>

<section class="card card--back" aria-label="Business card back">
  <div class="backdrop"></div>
  <div class="brand">
    <span class="brand__name">meridian systems</span>
  </div>
  <p class="tagline">We are an IT company specializing in Cloud Services<br>IT Managed Services, software and hardware</p>
</section>

</body>
</html>
```